New Business Card Design Project

Use the flyer uploaded and website www.brightoakbuilders.com for inspiration.
List Our Services on Backside of business cards
Marcus Delling
Harborline Builders Inc.
Licensed General Contractors
858-471-6093

Contact Information for Business Card

Use the flyer uploaded and website www.brightoakbuilders.com for inspiration. List Our Services on Backside of business cards Marcus Delling Harborline Builders Inc. Licensed General Contractors 858-471-6093

```html
<!DOCTYPE html>
<html lang="en">
<head>
<meta charset="utf-8">
<title>Harborline Builders – Business Card</title>
<link rel="stylesheet" href="https://fonts.googleapis.com/css2?family=Montserrat:wght@400;500;700;800&display=swap">
<style>
  :root {
    --stage: #2b2e33;
    --card-black: #1c1c1d;
    --card-white: #ffffff;
    --ink: #141414;
    --ink-soft: #3a3a3a;
    --on-dark: #f2f2f2;
    --on-dark-soft: #d4d4d4;
  }
  * { box-sizing: border-box; margin: 0; padding: 0; }
  html, body {
    width: 1200px; height: 900px; overflow: hidden;
    background: var(--stage);
    font-family: "Montserrat", sans-serif;
  }
  .canvas { position: relative; width: 1200px; height: 900px; }

  /* Front card */
  .card-front {
    position: absolute; left: 90px; top: 135px;
    width: 360px; height: 630px;
    border-radius: 28px; overflow: hidden;
    background: var(--card-white);
    box-shadow: 0 18px 40px rgba(0,0,0,.45);
  }
  .front-curve { position: absolute; inset: 0; }
  .person { position: absolute; left: 34px; top: 40px; }
  .person-name { font-size: 25px; font-weight: 800; color: var(--ink); letter-spacing: -.2px; }
  .person-title { font-size: 13px; font-weight: 500; color: var(--ink-soft); margin-top: 2px; }
  .contact-list { position: absolute; left: 34px; top: 196px; list-style: none; }
  .contact-list li {
    display: flex; align-items: center; gap: 10px;
    font-size: 13px; color: var(--ink); margin-bottom: 9px;
  }
  .contact-icon { width: 15px; height: 15px; flex: none; }
  .license { position: absolute; left: 34px; top: 308px; font-size: 12.5px; color: var(--ink); }
  .brand-front {
    position: absolute; left: 70px; right: 20px; top: 470px;
    text-align: center; color: var(--on-dark);
    font-size: 21px; font-weight: 500; letter-spacing: 2px; text-transform: uppercase;
    line-height: 1.35;
  }

  /* Back card */
  .card-back {
    position: absolute; left: 510px; top: 270px;
    width: 600px; height: 343px;
    border-radius: 26px;
    background: var(--card-black);
    box-shadow: 0 18px 40px rgba(0,0,0,.45);
    color: var(--on-dark);
  }
  .brand-back {
    position: absolute; right: 36px; top: 40px;
    font-size: 24px; font-weight: 500; letter-spacing: 2.5px; text-transform: uppercase;
    text-align: right;
  }
  .services { position: absolute; left: 300px; top: 104px; }
  .services-title {
    font-size: 16px; font-weight: 700; padding-bottom: 5px;
    border-bottom: 1.5px solid var(--on-dark); display: inline-block; margin-bottom: 8px;
  }
  .services-list { list-style: none; }
  .services-list li {
    font-size: 13px; color: var(--on-dark-soft); line-height: 1.55;
    padding-left: 13px; position: relative;
  }
  .services-list li::before {
    content: ""; position: absolute; left: 0; top: 8px;
    width: 5px; height: 5px; border-radius: 50%; background: var(--on-dark);
  }
</style>
</head>
<body>
<main class="canvas">

  <section class="card-front" aria-label="Business card front">
    <svg class="front-curve" width="360" height="630" viewBox="0 0 360 630" aria-hidden="true">
      <path d="M0 630 L0 520 C10 420 90 360 200 352 C270 348 330 370 360 395 L360 630 Z" fill="var(--card-black)"/>
    </svg>

    <div class="person">
      <h1 class="person-name">Marcus Delling</h1>
      <p class="person-title">Managing Director</p>
    </div>

    <ul class="contact-list">
      <li>
        <svg class="contact-icon" viewBox="0 0 16 16" aria-hidden="true"><circle cx="8" cy="8" r="8" fill="var(--ink)"/><path d="M5.2 4.2l1.4 1.6-.7 1c.5 1.1 1.3 1.9 2.4 2.4l1-.7 1.6 1.4-.8 1.2c-2.9-.4-5-2.5-5.4-5.4z" fill="#fff"/></svg>
        858-471-6093
      </li>
      <li>
        <svg class="contact-icon" viewBox="0 0 16 16" aria-hidden="true"><circle cx="8" cy="8" r="8" fill="var(--ink)"/><rect x="4" y="5.3" width="8" height="5.6" fill="none" stroke="#fff" stroke-width="1"/><path d="M4 5.5l4 3 4-3" fill="none" stroke="#fff" stroke-width="1"/></svg>
        info@brightoakbuilders.com
      </li>
      <li>
        <svg class="contact-icon" viewBox="0 0 16 16" aria-hidden="true"><circle cx="8" cy="8" r="8" fill="var(--ink)"/><circle cx="8" cy="8" r="4" fill="none" stroke="#fff" stroke-width="1"/><path d="M4 8h8M8 4c-2 2.4-2 5.6 0 8M8 4c2 2.4 2 5.6 0 8" fill="none" stroke="#fff" stroke-width=".8"/></svg>
        www.brightoakbuilders.com
      </li>
    </ul>

    <p class="license">CSLB Licensed No. #1048206</p>

    <p class="brand-front">Harborline Builders</p>
  </section>

  <section class="card-back" aria-label="Business card back">
    <p class="brand-back">Harborline Builders</p>
    <div class="services">
      <h2 class="services-title">Our Services</h2>
      <ul class="services-list">
        <li>Remodel: Kitchen &amp; Bath</li>
        <li>Painting: Interior &amp; Exterior</li>
        <li>Flooring: Carpet, Vinyl, Wood</li>
        <li>Window, Door Replacement</li>
        <li>Plumbing: Repair &amp; Upgrades</li>
        <li>Energy Efficient Upgrades</li>
        <li>Deck &amp; Patio construction</li>
        <li>Water &amp; Mold Damage</li>
        <li>Garage Renovation</li>
      </ul>
    </div>
  </section>

</main>
</body>
</html>
```